TK Homes - Stone Dorf Design

Looking for a double sides design, 1 side for my realestate and the other for home building. ( TK Homes on 1 side, Stone Dorf card on the other Side
Side 1 - Marek Tove ~ Vox Realty logo and Company ( the Property quarter )
Marek Tove
Marek@Marektove.example
IG - Marek_Bzq_Realtor
FB - marekt
Cell - 5558130467
3847 61 St Nw

Side 2
Marek Tove
5558130467
IG - Stonedorf_Bzq
Stonedorfdev@mailbox.example

Target Market(s)

Home buyers/ sellers

Industry/Entity Type

Home builders - Realestate

Contact Information for Business Card

Above

Requirements
Must have
• Black OR White background - my information -

```html
<!DOCTYPE html>
<html lang="en">
<head>
<meta charset="utf-8">
<title>TK Homes · Stone Dorf Design — Business Card</title>
<link href="https://fonts.googleapis.com/css2?family=Tinos:wght@400;700&family=Montserrat:wght@600&display=swap" rel="stylesheet">
<style>
  :root {
    --backdrop: #2b2b2e;
    --card: #1d1d21;
    --blue: #1a6fc4;
    --yellow: #f2c230;
    --white: #f1f1f1;
  }
  * { box-sizing: border-box; margin: 0; padding: 0; }
  html, body { width: 1200px; height: 780px; overflow: hidden; background: var(--backdrop); }
  .canvas {
    position: relative; width: 1200px; height: 780px;
    display: flex; align-items: center; justify-content: center; gap: 48px;
  }
  .card {
    position: relative; width: 540px; height: 309px;
    background: var(--card); overflow: hidden;
    box-shadow: 0 10px 30px rgba(0,0,0,.45);
    font-family: "Tinos", "Times New Roman", serif;
    color: var(--white);
  }
  .wordmark {
    position: absolute; font-family: "Tinos", "Times New Roman", serif;
    color: var(--blue); font-weight: 400; letter-spacing: 2px; text-transform: uppercase;
    display: flex; align-items: center; gap: 10px;
  }
  .wordmark__square { width: 14px; height: 14px; background: var(--blue); }
  .realty .wordmark { left: 150px; top: 34px; font-size: 32px; }
  .homebuild .wordmark { left: 40px; top: 38px; font-size: 30px; font-family: "Montserrat", sans-serif; font-weight: 600; letter-spacing: 1px; }
  .address { position: absolute; left: 180px; top: 90px; font-size: 15px; }
  .contacts { position: absolute; list-style: none; font-size: 15px; line-height: 22px; }
  .realty .contacts { left: 40px; top: 122px; }
  .homebuild .contacts { left: 40px; top: 118px; }
  .contacts li { display: flex; align-items: center; gap: 8px; }
  .icon { width: 13px; height: 13px; flex: none; }
  .icon--circle { border-radius: 50%; background: var(--blue); }
  .icon--square { background: var(--blue); }
  .signature { position: absolute; right: 58px; bottom: 52px; text-align: right; }
  .signature__name { font-weight: 700; font-size: 34px; line-height: 1; }
  .signature__first { color: var(--blue); }
  .signature__last { color: var(--yellow); }
  .signature__role { font-weight: 700; font-size: 16px; margin-top: 4px; }
  .accent-bars { position: absolute; right: 0; bottom: 40px; width: 40px; }
  .accent-bars span { display: block; height: 14px; background: var(--yellow); margin-bottom: 5px; margin-left: auto; }
  .accent-bars span:nth-child(1) { width: 28px; }
  .accent-bars span:nth-child(2) { width: 36px; }
  .accent-bars span:nth-child(3) { width: 22px; }
</style>
</head>
<body>
<main class="canvas">

  <section class="card realty" aria-label="Realty side">
    <div class="wordmark"><span class="wordmark__square"></span>Marek Tove</div>
    <p class="address">3847 61 St Nw</p>
    <ul class="contacts">
      <li><svg class="icon" viewBox="0 0 16 16"><path fill="#1a6fc4" d="M3 1l3 3-1.5 2a9 9 0 0 0 5.5 5.5L12 10l3 3-2 2C7 15 1 9 1 3z"/></svg>5558130467</li>
      <li><span class="icon icon--circle"></span>marekt</li>
      <li><span class="icon icon--square"></span>Marek_Bzq_Realtor</li>
      <li><svg class="icon" viewBox="0 0 16 16"><rect x="1" y="3" width="14" height="10" fill="#1a6fc4"/><path d="M1 3l7 6 7-6" stroke="#1d1d21" stroke-width="1.5" fill="none"/></svg>Marek@Marektove.example</li>
      <li><svg class="icon" viewBox="0 0 16 16"><circle cx="8" cy="8" r="6.5" fill="none" stroke="#1a6fc4" stroke-width="1.5"/><path d="M1.5 8h13M8 1.5c-3 3-3 10 0 13M8 1.5c3 3 3 10 0 13" stroke="#1a6fc4" stroke-width="1.2" fill="none"/></svg>www.marektove.example</li>
    </ul>
    <div class="signature">
      <p class="signature__name"><span class="signature__first">Marek</span> <span class="signature__last">Tove</span></p>
      <p class="signature__role">Director</p>
    </div>
    <div class="accent-bars"><span></span><span></span><span></span></div>
  </section>

  <section class="card homebuild" aria-label="Home building side">
    <div class="wordmark"><span class="wordmark__square"></span>Stone Dorf</div>
    <ul class="contacts">
      <li><svg class="icon" viewBox="0 0 16 16"><path fill="#1a6fc4" d="M3 1l3 3-1.5 2a9 9 0 0 0 5.5 5.5L12 10l3 3-2 2C7 15 1 9 1 3z"/></svg>5558130467</li>
      <li><span class="icon icon--square"></span>Stonedorf_Bzq</li>
      <li><svg class="icon" viewBox="0 0 16 16"><rect x="1" y="3" width="14" height="10" fill="#1a6fc4"/><path d="M1 3l7 6 7-6" stroke="#1d1d21" stroke-width="1.5" fill="none"/></svg>Stonedorfdev@mailbox.example</li>
    </ul>
    <div class="signature">
      <p class="signature__name"><span class="signature__first">Marek</span> <span class="signature__last">Tove</span></p>
      <p class="signature__role">Director</p>
    </div>
    <div class="accent-bars"><span></span><span></span><span></span></div>
  </section>

</main>
</body>
</html>
```